Stage Design Company Business Card

We are looking to step up up our business card design for our team.

We are a Full service Design and Consultation company for Stage and TV with an emphasis in Theatrical Lighting.

We like our materials to be clean and modern with solid colors free of patterns and gradients. Our brand consists of 4 primary colors Purple, Black, Grey, and White. Provided is our Word Mark as well as our Symbol Logo.

We would like our cards to leave an impression beyond the information, show our attention to design and detail, and make our marks an easily recognized feature (together or apart) for our clients.

We need a warm approachable comfortable feel for some clients, and a professional flair for the board member type clients.

Attached are our brand elements, and our existing cards to give a sense of our style and a glipse at the information we provide on our cards.

Target Market(s)

broad client base from church leaders to high school teachers and architects.

Industry/Entity Type

Business

Contact Information for Business Card

We format our phone number with periods not parenthesis or dashes. Information will be edited for each of our team members, and team member specific cards are not part of this scope, but rather a template so to speak.

Font styles to use
Sans Serif

Colors
6b449b
ffffff
000000
333333
aaaaaa

Requirements
Must have
• Wordmark and logo mark present (does not need to exist on the same side of card)
• Brand Colors,
• Name, Phone, Email, Address.
• Unique choices that make someone stop and take a second look
Nice to have
• It would be nice to somehow convey what we DO, as our brand name does not lend itself to this, outside of an obvious tagline though.....
• social media if not crowded. all of our handles match (instagram, twitter, facebook)
Should not have
• "clipart"

```html
<!DOCTYPE html>
<html lang="en">
<head>
<meta charset="utf-8">
<title>Orvane Business Card</title>
<link href="https://fonts.googleapis.com/css2?family=Source+Sans+3:wght@400;600;700&display=swap" rel="stylesheet">
<style>
  :root {
    --backdrop: #000000;
    --card: #333336;
    --ink: #efebe3;
    --rule: #48484c;
  }
  * { margin: 0; padding: 0; box-sizing: border-box; }
  html, body {
    width: 1200px; height: 899px; overflow: hidden;
    background: var(--backdrop);
    font-family: "Source Sans 3", sans-serif;
    color: var(--ink);
  }
  .canvas { position: relative; width: 1200px; height: 899px; }
  .card {
    position: absolute; top: 271px;
    width: 456px; height: 280px;
    background: var(--card);
    border-radius: 13px;
  }
  .card--front { left: 138px; }
  .card--back { left: 627px; }

  .brand-name {
    position: absolute; left: 20px; width: 190px; top: 132px;
    text-align: center; font-size: 24px; font-weight: 700;
    letter-spacing: 2px;
  }
  .divider {
    position: absolute; left: 213px; top: 73px;
    width: 1px; height: 145px; background: var(--rule);
  }
  .details { position: absolute; left: 248px; top: 76px; }
  .person-name { font-size: 18px; font-weight: 600; line-height: 20px; }
  .person-role { font-size: 13px; line-height: 16px; }
  .address { margin-top: 12px; font-size: 13px; line-height: 16px; }
  .contacts { margin-top: 10px; list-style: none; font-size: 13px; line-height: 16.5px; }
  .contacts li { display: flex; align-items: center; gap: 7px; }
  .contacts svg { width: 10px; height: 10px; fill: none; stroke: var(--ink); stroke-width: 1.4; }

  .mark-dot {
    position: absolute; left: 193px; top: 40px;
    width: 72px; height: 72px; border-radius: 50%;
    background: var(--ink);
  }
  .wordmark {
    position: absolute; left: 0; right: 0; top: 186px;
    text-align: center; font-size: 28px; font-weight: 400;
    letter-spacing: 14px; text-indent: 14px; line-height: 32px;
  }
  .tagline {
    position: absolute; left: 0; right: 0; top: 229px;
    text-align: center; font-size: 12.5px; font-weight: 700;
    line-height: 17px; text-transform: uppercase;
  }
</style>
</head>
<body>
<main class="canvas">
  <section class="card card--front">
    <div class="brand-name">ORVANE</div>
    <div class="divider"></div>
    <div class="details">
      <p class="person-name">Marcus Ellery</p>
      <p class="person-role">Managing Director</p>
      <p class="address">418 Marlow Street<br>Fairhaven, 204417.</p>
      <ul class="contacts">
        <li><svg viewBox="0 0 10 10"><path d="M2 1l2 2-1 1.2c.7 1.3 1.5 2.1 2.8 2.8L7 6l2 2-1.3 1.3C4.5 9 1 5.5.7 2.3z" fill="var(--ink)" stroke="none"/></svg>044.218.605.731</li>
        <li><svg viewBox="0 0 10 10"><rect x="1" y="2.2" width="8" height="5.6" fill="var(--ink)" stroke="none"/><path d="M1 2.5l4 3 4-3" stroke="var(--card)"/></svg>hello@orvane.com</li>
        <li><svg viewBox="0 0 10 10"><path d="M4.3 5.7l1.4-1.4M3.6 4.2L2.2 5.6a1.5 1.5 0 002.2 2.2l1.4-1.4M6.4 5.8l1.4-1.4a1.5 1.5 0 00-2.2-2.2L4.2 3.6"/></svg>www.orvane.com</li>
      </ul>
    </div>
  </section>

  <section class="card card--back">
    <div class="mark-dot"></div>
    <div class="wordmark">ORVANE</div>
    <p class="tagline">Design and consultation company for stage and<br>TV with an emphasis in theatrical lighting.</p>
  </section>
</main>
</body>
</html>
```